Harborline Renewal Business Card Design

Professional and clean design. The design colors should flow with the logo. Two-sided card with the website on the back which is:

www.HarborlineRenewal.example.

"Specializing in Water Damage Restoration"

On the front I need the name, email, phone, and logo.

Name: Darnell Quisby
Email: Darnell@HarborlineRenewal.example
Phone: 555-318-2046 for now

I only have the Preview and Thumbnail right now but should have the source files uploaded within a day or two.

Target Market(s)

Flood victims, home owners with water damage from busted pipes etc...

Industry/Entity Type

Business

Contact Information for Business Card

Name: Darnell Quisby

Font styles to use
Serif
Sans Serif

Requirements
Must have
• Business Card Details Info

```html
<!DOCTYPE html>
<html lang="en">
<head>
<meta charset="utf-8">
<title>Harborline Renewal Business Card</title>
<link rel="stylesheet" href="https://fonts.googleapis.com/css2?family=Cinzel:wght@400&family=Open+Sans:wght@400;600;700&display=swap">
<style>
  :root {
    --page-bg: #ececec;
    --card-dark: #1c1c1d;
    --brand-blue: #3a9ad9;
    --brand-blue-deep: #2f8ccc;
    --text-light: #f2f2f2;
    --text-dark: #10233a;
    --band-white: #ffffff;
    --divider: #4a4a4c;
  }
  * { box-sizing: border-box; margin: 0; padding: 0; }
  html, body {
    width: 1200px; height: 844px; overflow: hidden;
    background: var(--page-bg);
  }
  .canvas {
    position: relative; width: 1200px; height: 844px;
    display: flex; align-items: center; justify-content: center; gap: 40px;
  }
  .card {
    position: relative; width: 520px; height: 297px;
    box-shadow: 0 6px 18px rgba(0,0,0,0.18);
    overflow: hidden;
  }

  /* Front side */
  .card--front { background: var(--card-dark); }
  .front-brand {
    position: absolute; left: 0; top: 0; width: 236px; height: 100%;
    display: flex; flex-direction: column; align-items: center; justify-content: center; gap: 12px;
  }
  .brand-dot {
    width: 50px; height: 50px; border-radius: 50%;
    background: var(--brand-blue);
  }
  .front-brand__name {
    font-family: "Cinzel", serif; font-weight: 400;
    color: var(--brand-blue); text-align: center; line-height: 1.1;
  }
  .front-brand__name .line-1 { display: block; font-size: 26px; letter-spacing: 1px; }
  .front-brand__name .line-2 { display: block; font-size: 12px; letter-spacing: 4px; }
  .front-divider {
    position: absolute; left: 244px; top: 72px; width: 1px; height: 150px;
    background: var(--divider);
  }
  .front-contact {
    position: absolute; left: 262px; top: 96px; right: 24px;
    font-family: "Open Sans", sans-serif; color: var(--text-light);
  }
  .contact-name { font-size: 17px; font-weight: 700; margin-bottom: 18px; white-space: nowrap; }
  .contact-row {
    display: flex; align-items: center; gap: 8px;
    font-size: 11px; line-height: 1.6; white-space: nowrap;
  }
  .contact-row svg { width: 11px; height: 11px; flex: none; fill: var(--text-light); }

  /* Back side */
  .card--back { background: linear-gradient(160deg, var(--brand-blue) 0%, var(--brand-blue-deep) 100%); }
  .back-brand {
    position: absolute; left: 0; right: 0; top: 38px;
    font-family: "Cinzel", serif; font-weight: 400; color: var(--band-white);
    text-align: center; line-height: 1.05;
  }
  .back-brand .line-1 { display: block; font-size: 46px; letter-spacing: 2px; }
  .back-brand .line-2 { display: block; font-size: 17px; letter-spacing: 7px; }
  .back-band {
    position: absolute; left: 0; right: 0; top: 150px; height: 70px;
    background: var(--band-white);
    display: flex; align-items: flex-start; justify-content: center; padding-top: 12px;
    font-family: "Open Sans", sans-serif; font-size: 12.5px; color: var(--brand-blue);
  }
  .back-tagline {
    position: absolute; left: 0; right: 0; top: 244px;
    text-align: center;
    font-family: "Open Sans", sans-serif; font-weight: 700; font-size: 13px;
    color: var(--text-dark);
  }
</style>
</head>
<body>
<main class="canvas">
  <section class="card card--front" aria-label="Business card front">
    <div class="front-brand">
      <span class="brand-dot" aria-hidden="true"></span>
      <p class="front-brand__name"><span class="line-1">HARBORLINE</span><span class="line-2">RENEWAL</span></p>
    </div>
    <div class="front-divider" aria-hidden="true"></div>
    <div class="front-contact">
      <p class="contact-name">Darnell Quisby</p>
      <p class="contact-row">
        <svg viewBox="0 0 24 24" aria-hidden="true"><path d="M6.6 10.8a15.1 15.1 0 0 0 6.6 6.6l2.2-2.2a1 1 0 0 1 1-.25 11.4 11.4 0 0 0 3.6.57 1 1 0 0 1 1 1V20a1 1 0 0 1-1 1A17 17 0 0 1 3 4a1 1 0 0 1 1-1h3.5a1 1 0 0 1 1 1c0 1.25.2 2.45.57 3.57a1 1 0 0 1-.25 1z"/></svg>
        <span>555-318-2046</span>
      </p>
      <p class="contact-row">
        <svg viewBox="0 0 24 24" aria-hidden="true"><path d="M2 5h20v14H2z M2 5l10 8 10-8" fill="none" stroke="#f2f2f2" stroke-width="2"/></svg>
        <span>Darnell@HarborlineRenewal.example</span>
      </p>
    </div>
  </section>

  <section class="card card--back" aria-label="Business card back">
    <p class="back-brand"><span class="line-1">HARBORLINE</span><span class="line-2">RENEWAL</span></p>
    <div class="back-band">www.HarborlineRenewal.example</div>
    <p class="back-tagline">Specializing in Water Damage Restoration</p>
  </section>
</main>
</body>
</html>
```